Promotional Postcard for Mountain Bike Stunt Show

PLEASE DOWNLOAD ATTACHED ZIP FILE

This will be on a larger postcard size: 4ā€ x 9ā€ - front and back will be completely covered in text and pictures. I’m going to mail it out in envelopes.

Overview: This is promotional postcard for my mountain bike stunt show. It will be filled with text and pictures to attract clients into booking my show. It must look clean and professional. Remember: This is an action stunt show based out of the mountain states region so it must look exciting, rugged, clean and professional :)

A few additional notes: I'd also like to see the logo picture 1 used on the front to display the name of my show but then fade out to the right into whatever else you want to fit. As far as all of the text, try to put that in "dead space" in the pictures if there open air or in Picture 3 where theres an opportunity to fade out the unwanted trailer and grass showing and put text in there "action packed etc etc"

Target Market(s)

Trade shows, fairs, schools, festivals, agricultural fairs, corporate events

Industry/Entity Type

Entertainment Industry

Colors

Designer to choose colors to be used in the design.

Requirements
Must have
• FOLLOW INSTRUCTIONS IN MY ATTACHED ZIP FILE
Nice to have
• I think I'd like a dark theme/layout to the card :)

```html
<!DOCTYPE html>
<html lang="en">
<head>
<meta charset="utf-8">
<title>Mountain Bike Trials Stunt Show – Postcard</title>
<link href="https://fonts.googleapis.com/css2?family=Black+Ops+One&family=Bangers&family=Uncial+Antiqua&family=Roboto+Condensed:wght@300;400&family=Open+Sans:wght@600;700;800&family=Kaushan+Script&display=swap" rel="stylesheet">
<style>
  :root{
    --page:#6a9bd1;
    --paper:#e7e7e7;
    --paper-white:#f7f7f7;
    --sky:#1e9ad8;
    --sky-deep:#1673b3;
    --navy:#23506f;
    --red:#a5121c;
    --red-bright:#c8141e;
    --ink:#2b2b2b;
    --ink-soft:#4a4a4a;
    --white:#ffffff;
    --badge:#c9ced4;
  }
  *{box-sizing:border-box;margin:0;padding:0}
  html,body{width:1200px;height:791px;overflow:hidden;background:var(--page)}
  .canvas{position:relative;width:1200px;height:791px}
  .card{position:absolute;left:104px;width:992px;height:350px;overflow:hidden;background:var(--paper);box-shadow:0 4px 10px rgba(0,0,0,.25)}
  .card--front{top:28px}
  .card--back{top:412px;background:var(--paper-white)}
  .card svg.shapes{position:absolute;inset:0;width:992px;height:350px}

  /* Front */
  .headline{position:absolute;left:300px;top:12px;width:380px;text-align:center;font-family:"Black Ops One",sans-serif;color:var(--red);line-height:1}
  .headline span{display:block;font-size:40px}
  .headline .l1{margin-bottom:10px}
  .headline .l2{margin-bottom:8px;letter-spacing:1px}
  .delivers{position:absolute;left:330px;top:168px;width:330px;text-align:center;font-family:"Bangers",sans-serif;color:var(--white);line-height:.95;letter-spacing:3px;
    text-shadow:-3px -3px 0 var(--navy),3px -3px 0 var(--navy),-3px 3px 0 var(--navy),3px 3px 0 var(--navy),0 4px 0 var(--navy),4px 0 0 var(--navy),-4px 0 0 var(--navy),0 -4px 0 var(--navy)}
  .delivers span{display:block;font-size:48px}
  .delivers .big{font-size:52px}
  .tagline{position:absolute;left:70px;top:240px;width:230px;text-align:center;font-family:"Uncial Antiqua",serif;color:var(--navy);font-size:26px;line-height:1.12}
  .label{position:absolute;font-family:"Open Sans",sans-serif;font-weight:700;color:var(--white);text-align:center;line-height:1.15;padding:3px 6px}
  .label--blue{background:var(--sky);font-size:11px}
  .label--red{background:var(--red-bright);font-size:10px}

  /* Back */
  .blurb{position:absolute;left:410px;top:10px;width:222px;font-family:"Roboto Condensed",sans-serif;font-weight:300;font-size:16px;line-height:25px;color:var(--ink);text-align:justify;text-align-last:left}
  .show-title{position:absolute;left:660px;top:40px;width:320px;text-align:center;color:var(--white)}
  .show-title .owner{display:block;font-family:"Kaushan Script",cursive;font-size:22px}
  .show-title .name{display:block;font-family:"Open Sans",sans-serif;font-weight:800;font-size:19px;letter-spacing:1px;line-height:1.2}
  .handle{position:absolute;left:650px;top:125px;display:flex;align-items:center;gap:5px;font-family:"Open Sans",sans-serif;font-weight:700;font-size:11px;color:var(--ink)}
  .handle i{display:inline-block;width:14px;height:14px;background:var(--red)}
  .site-top{position:absolute;left:800px;top:128px;font-family:"Open Sans",sans-serif;font-weight:700;font-size:11px;color:var(--ink)}
  .booking{position:absolute;left:652px;top:150px;font-family:"Open Sans",sans-serif}
  .booking h2{font-size:19px;line-height:24px;font-weight:800;color:var(--sky)}
  .booking h3{font-size:19px;line-height:24px;font-weight:800;color:var(--red);margin-top:2px}
  .booking ul{list-style:none;margin-top:4px}
  .booking li{display:flex;align-items:center;gap:14px;font-size:20px;font-weight:700;color:var(--ink);height:28px;white-space:nowrap}
  .booking li svg{width:20px;height:20px;flex:none}
  .venues-banner{position:absolute;left:20px;top:242px;height:32px;width:400px;padding-left:24px;font-family:"Open Sans",sans-serif;font-weight:700;font-size:16px;color:var(--white);line-height:32px}
  .venues{position:absolute;left:20px;top:288px;width:960px;height:40px;display:flex;align-items:center;gap:12px}
  .venue{flex:none;background:var(--badge)}
  .venue--round{width:40px;height:40px;border-radius:50%}
  .venue--wide{height:28px}
</style>
</head>
<body>
<div class="canvas">

  <section class="card card--front">
    <svg class="shapes" viewBox="0 0 992 350">
      <defs>
        <linearGradient id="photoRider" x1="0" y1="0" x2="0" y2="1">
          <stop offset="0" stop-color="#7fc3ee"/>
          <stop offset=".55" stop-color="#a9b8c4"/>
          <stop offset=".8" stop-color="#6d9b4a"/>
          <stop offset="1" stop-color="#b33a2c"/>
        </linearGradient>
        <linearGradient id="bandBlue" x1="0" y1="0" x2="1" y2="0">
          <stop offset="0" stop-color="#1673b3"/>
          <stop offset=".5" stop-color="#2aa3e0"/>
          <stop offset="1" stop-color="#1e8ccc"/>
        </linearGradient>
        <linearGradient id="hexA" x1="0" y1="0" x2="0" y2="1"><stop offset="0" stop-color="#3b78b5"/><stop offset="1" stop-color="#7fa35a"/></linearGradient>
        <linearGradient id="hexB" x1="0" y1="0" x2="0" y2="1"><stop offset="0" stop-color="#e9ecef"/><stop offset="1" stop-color="#8a9aa8"/></linearGradient>
        <linearGradient id="hexC" x1="0" y1="0" x2="0" y2="1"><stop offset="0" stop-color="#9aa1a8"/><stop offset="1" stop-color="#3a3c40"/></linearGradient>
      </defs>
      <rect width="992" height="350" fill="var(--paper)"/>
      <path d="M0,250 C60,300 170,300 250,340 L0,350 Z" fill="var(--sky)"/>
      <path d="M0,268 C120,262 250,200 330,60" fill="none" stroke="var(--navy)" stroke-width="16"/>
      <g role="img" aria-label="Trials rider airborne over a ramp in front of a fair crowd">
        <path d="M0,0 H345 C310,80 250,160 170,205 C110,238 50,250 0,248 Z" fill="url(#photoRider)"/>
      </g>
      <path d="M345,0 C310,80 250,160 170,205 C110,238 50,250 0,248" fill="none" stroke="var(--sky)" stroke-width="10"/>
      <path d="M830,0 H992 V350 H820 C745,270 745,90 830,0 Z" fill="url(#bandBlue)"/>
      <path d="M800,0 C725,95 725,260 790,350" fill="none" stroke="var(--navy)" stroke-width="14"/>
      <path d="M815,0 C742,95 742,260 806,350" fill="none" stroke="var(--white)" stroke-width="3"/>
      <rect y="340" width="992" height="10" fill="var(--sky)"/>
      <g role="img" aria-label="Rider giving a high five to a young fan">
        <polygon points="948,75 918,127 858,127 828,75 858,23 918,23" fill="url(#hexA)" stroke="var(--white)" stroke-width="4"/>
      </g>
      <g role="img" aria-label="Kids at a table during an autograph session">
        <polygon points="862,170 832,222 772,222 742,170 772,118 832,118" fill="url(#hexB)" stroke="var(--white)" stroke-width="4"/>
      </g>
      <g role="img" aria-label="Bagged giveaway items and water bottles">
        <polygon points="942,268 912,320 852,320 822,268 852,216 912,216" fill="url(#hexC)" stroke="var(--white)" stroke-width="4"/>
      </g>
    </svg>

    <h1 class="headline">
      <span class="l1">AWESOME</span>
      <span class="l2">ENTERTAINMENT</span>
      <span class="l3">FOR YOUR EVENT!</span>
    </h1>
    <p class="delivers"><span>THIS</span><span>SHOW</span><span class="big">DELIVERS!</span></p>
    <p class="tagline">Loads of<br>high-energy<br>action!</p>

    <p class="label label--blue" style="left:692px;top:68px;width:114px">AUDIENCE<br>ENGAGEMENT!</p>
    <p class="label label--red" style="left:856px;top:164px;width:122px">Meet n' greet<br>autograph session</p>
    <p class="label label--blue" style="left:702px;top:258px;width:92px">FREE<br>GIVEAWAYS!</p>
  </section>

  <section class="card card--back">
    <svg class="shapes" viewBox="0 0 992 350">
      <defs>
        <linearGradient id="photoHall" x1="0" y1="0" x2="0" y2="1">
          <stop offset="0" stop-color="#d9dde1"/>
          <stop offset=".5" stop-color="#a9aeb3"/>
          <stop offset=".8" stop-color="#c6c2bc"/>
          <stop offset="1" stop-color="#e6e6e6"/>
        </linearGradient>
        <linearGradient id="photoFade" x1="0" y1="0" x2="1" y2="0">
          <stop offset=".8" stop-color="#f7f7f7" stop-opacity="0"/>
          <stop offset="1" stop-color="#f7f7f7"/>
        </linearGradient>
        <linearGradient id="photoMountain" x1="0" y1="0" x2="0" y2="1">
          <stop offset="0" stop-color="#4c7fb3"/>
          <stop offset=".6" stop-color="#9fb9cf"/>
          <stop offset="1" stop-color="#e8eef3"/>
        </linearGradient>
      </defs>
      <rect width="992" height="350" fill="var(--paper-white)"/>
      <g role="img" aria-label="Rider balancing a trials bike on a red obstacle box inside an exhibition hall with a seated crowd">
        <rect width="405" height="262" fill="url(#photoHall)"/>
        <rect width="405" height="262" fill="url(#photoFade)"/>
      </g>
      <g role="img" aria-label="Rider on a trials bike on a rocky ledge with snowy mountains behind">
        <rect x="632" width="360" height="145" fill="url(#photoMountain)"/>
      </g>
      <path d="M20,242 H420 L410,274 H20 Z" fill="var(--red)"/>
      <rect y="340" width="992" height="10" fill="var(--sky)"/>
    </svg>

    <p class="blurb">Danny is a pro, showcasing the most technical aspects of mountain biking as he rides over seemingly impossible obstacles with his bike. Danny's charismatic personality, coupled with his 20 years of trials experience, makes for an unforgettable stunt display of balance and skill.</p>

    <p class="show-title"><span class="owner">Danny Kessler's</span><span class="name">MOUNTAIN BIKE TRIALS<br>STUNT SHOW</span></p>
    <p class="handle"><i></i>kesslertrials</p>
    <p class="site-top">www.kesslertrials.com</p>

    <div class="booking">
      <h2>Booking Info:</h2>
      <h3>Danny Kessler</h3>
      <ul>
        <li><svg viewBox="0 0 20 20"><circle cx="10" cy="10" r="9" fill="var(--red)"/><path d="M5,8 Q10,4 15,8 L13,10 L11,8.5 H9 L7,10 Z M6,11 H14 V14 H6 Z" fill="#fff"/></svg>(555) 014-2273</li>
        <li><svg viewBox="0 0 20 20"><circle cx="10" cy="10" r="9" fill="var(--red)"/><rect x="5" y="6.5" width="10" height="7" fill="#fff"/><path d="M5,6.5 L10,10.5 L15,6.5" fill="none" stroke="var(--red)" stroke-width="1.2"/></svg>danny@kesslertrials.com</li>
        <li><svg viewBox="0 0 20 20"><circle cx="10" cy="10" r="9" fill="var(--red)"/><g fill="none" stroke="#fff" stroke-width="1.2"><circle cx="10" cy="10" r="5.5"/><ellipse cx="10" cy="10" rx="2.5" ry="5.5"/><path d="M4.5,10 H15.5"/></g></svg>www.kesslertrials.com</li>
      </ul>
    </div>

    <p class="venues-banner">Past venues where Danny has performed:</p>
    <div class="venues">
      <span class="venue venue--round"></span>
      <span class="venue venue--round"></span>
      <span class="venue venue--round"></span>
      <span class="venue venue--round"></span>
      <span class="venue venue--round"></span>
      <span class="venue venue--wide" style="width:86px"></span>
      <span class="venue venue--wide" style="width:40px;height:36px"></span>
      <span class="venue venue--wide" style="width:90px"></span>
      <span class="venue venue--wide" style="width:80px"></span>
      <span class="venue venue--wide" style="width:120px;height:18px"></span>
      <span class="venue venue--wide" style="width:86px;height:20px"></span>
      <span class="venue venue--wide" style="width:100px;height:16px"></span>
    </div>
  </section>

</div>
</body>
</html>
```